Kestrada LLC, needs a web page no more than 5 pages (for now)

Kestrada is a general contractor. Our services include general contracting, design-build construction, disaster recovery and environmental remediation. Our main clients are PMX, TQ, State and Local Gov't Agencies, Hospitals and Schools. Kestrada is also a SDVOSB.

```html
<!DOCTYPE html>
<html lang="en">
<head>
<meta charset="UTF-8">
<title>Kestrada – Building Trust. Delivering Value.</title>
<link href="https://fonts.googleapis.com/css2?family=Playfair+Display:wght@700;800;900&family=Poppins:wght@400;500;600&display=swap" rel="stylesheet">
<style>
:root{
  --gold:#d1ad45;
  --gold-dark:#b8922c;
  --gold-light:#f1dc83;
  --mustard:#c7a03f;
  --cream:#fcfbf1;
  --ink:#111111;
  --text:#333333;
  --white:#ffffff;
  --photo-dark:#4d4a44;
  --btn-grad:linear-gradient(90deg,#c9a33c,#f2dc83);
}
*{margin:0;padding:0;box-sizing:border-box}
html,body{width:1200px;height:4101px;overflow:hidden}
body{position:relative;background:var(--white);font-family:"Poppins",sans-serif;color:var(--text)}
.abs{position:absolute}
.serif{font-family:"Playfair Display",serif;font-weight:900;color:var(--ink);text-transform:uppercase;letter-spacing:.5px}
.photo{position:absolute}
.btn{position:absolute;display:flex;align-items:center;justify-content:center;border-radius:20px;font-size:11px;font-weight:500;text-transform:uppercase;color:var(--white);background:var(--btn-grad)}
.btn.outline{background:var(--white);color:var(--ink)}

/* header */
.site-header{position:absolute;left:0;top:0;width:1200px;height:78px;background:var(--white)}
.brand{position:absolute;display:flex;align-items:center;gap:8px;font-family:"Poppins",sans-serif;font-weight:600;text-transform:uppercase}
.brand .dot{border-radius:50%;border:3px solid var(--gold)}
.nav a{position:absolute;top:32px;font-size:11px;color:var(--ink);text-decoration:none;text-transform:uppercase}
.home-btn{position:absolute;left:360px;top:16px;width:48px;height:48px;border-radius:50%;background:#fff;box-shadow:0 0 12px rgba(0,0,0,.1)}

/* hero */
.hero{position:absolute;left:0;top:78px;width:1200px;height:720px;background:linear-gradient(110deg,#3f3d39 0%,#6b665c 45%,#a48a5c 70%,#8a8175 100%)}
.hero-title{position:absolute;left:83px;top:272px;font-size:56px;line-height:58px;color:var(--white);border-left:4px solid var(--gold);padding-left:6px;margin-left:-10px}
.hero-text{position:absolute;left:76px;top:408px;width:510px;font-size:12.5px;line-height:19px;color:var(--white)}
.section-label{position:absolute;font-family:"Playfair Display",serif;font-weight:800;font-size:13px;text-transform:uppercase;color:var(--ink)}
.section-label::before{content:"";position:absolute;left:-16px;top:-18px;width:34px;height:34px;border-top:3px solid var(--gold);border-left:3px solid var(--gold);border-radius:50%;transform:rotate(15deg)}
h2{position:absolute;font-size:38px;line-height:40px}
.body-text{position:absolute;font-size:10.5px;line-height:16.5px;color:var(--text)}

/* services */
.service-card{position:absolute;top:1477px;width:238px;height:329px;background:var(--white)}
.service-card .photo{left:0;top:0;width:238px;height:189px}
.service-card h3{position:absolute;left:14px;top:214px;font-size:13px;line-height:18px}
.service-card p{position:absolute;left:14px;width:212px;font-size:10px;line-height:16px}

/* clients */
.clients{position:absolute;left:0;top:1830px;width:1200px;height:665px;background:var(--mustard)}
.client{position:absolute;top:2161px;width:200px;margin-left:-100px;text-align:center}
.seal{position:absolute;left:41px;top:0;width:118px;height:118px;border-radius:50%;background:#f5f0e2;border:5px solid #fff;box-shadow:0 0 0 2px #9a7a27}
.seal-num{position:absolute;left:88px;top:108px;width:24px;height:24px;border-radius:50%;background:var(--gold);color:#fff;font-size:11px;font-weight:600;line-height:24px}
.client h4{position:absolute;left:0;top:155px;width:200px;font-family:"Playfair Display",serif;font-weight:800;font-size:14px;line-height:18px;color:var(--white);text-transform:uppercase}

/* credentials */
.checklist{position:absolute;left:177px;top:2938px;list-style:none;font-size:10.5px;line-height:17px}
.checklist li{display:flex;align-items:center;gap:7px}
.checklist svg{flex:none}

/* contact */
.field{position:absolute;height:34px;border:1px solid #d9d3bd;border-radius:17px;font-size:8.5px;color:#888;padding:11px 16px}

/* footer */
.footer-col h5{position:absolute;font-family:"Playfair Display",serif;font-weight:800;font-size:13px;color:var(--white);text-transform:uppercase;border-left:2px solid var(--gold);padding-left:8px}
.footer-col a,.footer-col span{position:absolute;font-size:10px;color:var(--white);text-decoration:none}
.social{position:absolute;top:3886px;width:24px;height:24px;border-radius:50%;background:#222}
</style>
</head>
<body>

<!-- header -->
<header class="site-header">
  <div class="brand" style="left:75px;top:20px;font-size:18px;color:var(--ink)">
    <span class="dot" style="width:30px;height:30px"></span>Kestrada
  </div>
  <div class="home-btn">
    <svg class="abs" style="left:17px;top:17px" width="14" height="14" viewBox="0 0 14 14"><path d="M7 1 1 6.5h2V13h3V9h2v4h3V6.5h2z" fill="#d1ad45"/></svg>
  </div>
  <nav class="nav">
    <a style="left:452px">About Us</a>
    <a style="left:559px">Services</a>
    <a style="left:661px">Clients</a>
    <a style="left:755px">Certifications</a>
  </nav>
  <svg class="abs" style="left:908px;top:26px" width="24" height="24" viewBox="0 0 24 24"><clipPath id="flag"><circle cx="12" cy="12" r="12"/></clipPath><g clip-path="url(#flag)"><rect width="24" height="8" fill="#000"/><rect y="8" width="24" height="8" fill="#dd0000"/><rect y="16" width="24" height="8" fill="#ffce00"/></g></svg>
  <span class="abs" style="left:941px;top:30px;font-size:11px;color:var(--ink)">DE ⌄</span>
  <div class="btn" style="left:996px;top:21px;width:128px;height:38px">Contact Us</div>
</header>

<!-- hero -->
<section class="hero">
  <div class="photo" role="img" aria-label="Two engineers in hard hats and safety vests reviewing plans at a construction site" style="inset:0;background:linear-gradient(110deg,#3f3d39 0%,#6b665c 45%,#a48a5c 70%,#8a8175 100%)"></div>
  <div class="abs" style="left:952px;top:524px;font-size:17px;line-height:18px;color:#fff;font-weight:500">KESTRADA<br><span style="font-size:24px;line-height:26px">VIDEO</span></div>
  <svg class="abs" style="left:1040px;top:512px" width="62" height="62" viewBox="0 0 62 62"><circle cx="31" cy="31" r="31" fill="#e9d27a"/><path d="M25 21v20l16-10z" fill="#111"/></svg>
</section>
<h1 class="serif hero-title">Building Trust.<br>Delivering Value.</h1>
<p class="hero-text">Kestrada is a Service-Disabled Veteran-Owned Small Business (SDVOSB) providing full-service construction solutions — from design-build projects to disaster recovery and environmental remediation.</p>
<div class="btn" style="left:76px;top:487px;width:128px;height:37px">Learn More</div>
<div class="btn outline" style="left:221px;top:487px;width:126px;height:37px">Contact Us</div>

<svg class="abs" style="left:0;top:630px" width="1200" height="160" viewBox="0 0 1200 160">
  <path d="M0 6 Q420 95 855 150 Q1040 60 1200 0 V30 Q1040 90 855 160 Q420 120 0 30Z" fill="#d1ad45"/>
  <path d="M0 6 Q420 95 855 150 Q1040 60 1200 0 V0 H0Z" fill="none"/>
  <path d="M0 0 V10 Q420 95 855 145 Q1040 55 1200 4 V160 H0Z" fill="#fff"/>
</svg>
<svg class="abs" style="left:577px;top:703px" width="42" height="60" viewBox="0 0 42 60"><rect x="1" y="1" width="40" height="58" rx="20" fill="#fff" stroke="#ddd"/><path d="M21 20v18M15 32l6 6 6-6" stroke="#111" stroke-width="1.6" fill="none"/></svg>

<!-- about -->
<div class="abs" style="left:0;top:1225px;width:1200px;height:605px;background:var(--cream)"></div>
<div class="abs" style="left:162px;top:823px;width:228px;height:213px;background:var(--gold-light)"></div>
<div class="photo" role="img" aria-label="Site supervisor with a radio and a colleague holding a tablet, both in hard hats" style="left:189px;top:845px;width:358px;height:446px;background:linear-gradient(160deg,#d8a54a,#8a7a66 55%,#5e6d7d)"></div>
<div class="section-label" style="left:673px;top:940px">About Us</div>
<h2 class="serif" style="left:657px;top:968px">Who We Are</h2>
<p class="body-text" style="left:657px;top:1020px;width:372px">Kestrada is a trusted general contractor serving federal, state, and local government agencies as well as hospitals, schools, and institutions across the U.S. With a strong foundation in construction excellence and a commitment to integrity, we deliver projects that meet the highest standards of safety, quality, and compliance.</p>
<div class="btn" style="left:656px;top:1122px;width:127px;height:38px">Read More</div>

<!-- services -->
<div class="section-label" style="left:571px;top:1383px">Services</div>
<h2 class="serif" style="left:0;width:1200px;text-align:center;top:1412px">What We Do</h2>

<article class="service-card" style="left:100px">
  <div class="photo" role="img" aria-label="Workers on formwork at a building site" style="background:linear-gradient(180deg,#7fa6d6,#a69a7e 60%,#7a5a22)"></div>
  <h3 class="serif">General Contracting</h3>
  <p style="top:1733px;top:256px">Full-spectrum construction management ensuring projects are delivered on time and on budget.</p>
</article>
<article class="service-card" style="left:355px">
  <div class="photo" role="img" aria-label="Architects reviewing design drawings at a desk" style="background:linear-gradient(180deg,#e6e6e8,#b8b4aa 60%,#8a8e98)"></div>
  <h3 class="serif">Design-Build<br>Construction</h3>
  <p style="top:256px">Integrated design and construction solutions for streamlined project delivery.</p>
</article>
<article class="service-card" style="left:608px">
  <div class="photo" role="img" aria-label="Environmental technicians checking equipment in the field" style="background:linear-gradient(180deg,#5b5f52,#8a8a5a 60%,#3e3b33)"></div>
  <h3 class="serif">Environmental<br>Remediation</h3>
  <p style="top:256px">Safe, compliant cleanup of hazardous materials to restore healthy environments.</p>
</article>
<article class="service-card" style="left:861px">
  <div class="photo" role="img" aria-label="Collapsed building after a natural disaster" style="background:linear-gradient(180deg,#6f9ad0,#a39a8e 55%,#6d655c)"></div>
  <h3 class="serif">Disaster Recovery</h3>
  <p style="top:256px">Rapid response and reliable recovery services for communities and facilities impacted by natural disasters.</p>
</article>

<!-- clients -->
<section class="clients" role="img" aria-label="Gold-toned background of a contractor reviewing plans">
  <svg class="abs" style="left:0;top:0" width="1200" height="150" viewBox="0 0 1200 150">
    <path d="M0 0H1200V25L764 112 0 0Z" fill="#fcfbf1"/>
    <path d="M0 0 764 112 1200 25V45L764 134 0 20Z" fill="#f1dc83"/>
  </svg>
</section>
<div class="section-label" style="left:577px;top:2056px;color:#fff">Clients</div>
<h2 class="serif" style="left:0;width:1200px;text-align:center;top:2082px;color:#fff">Who We Serve</h2>

<div class="client" style="left:177px"><div class="seal"></div><div class="seal-num">01</div><h4>Department<br>of Logistics<br>(PMX)</h4></div>
<div class="client" style="left:388px"><div class="seal"></div><div class="seal-num">02</div><h4>Department<br>of Service<br>Affairs (TQ)</h4></div>
<div class="client" style="left:600px"><div class="seal"></div><div class="seal-num">03</div><h4>State &amp; Local<br>Government<br>Agencies</h4></div>
<div class="client" style="left:812px"><div class="seal"></div><div class="seal-num">04</div><h4>Hospitals &amp;<br>Healthcare<br>Facilities</h4></div>
<div class="client" style="left:1023px"><div class="seal"></div><div class="seal-num">05</div><h4>Schools &amp;<br>Educational<br>Institutions</h4></div>
<svg class="abs" style="left:0;top:2205px" width="1200" height="30" viewBox="0 0 1200 30">
  <g fill="none" stroke="#fff" stroke-width="4" stroke-linejoin="miter">
    <path d="M262 4l11 11-11 11M276 4l11 11-11 11"/>
    <path d="M480 4l11 11-11 11M494 4l11 11-11 11"/>
    <path d="M687 4l11 11-11 11M701 4l11 11-11 11"/>
    <path d="M907 4l11 11-11 11M921 4l11 11-11 11"/>
  </g>
</svg>

<!-- credentials -->
<div class="section-label" style="left:196px;top:2726px">Certifications</div>
<h2 class="serif" style="left:181px;top:2754px">Our Credentials</h2>
<p class="body-text" style="left:177px;top:2814px;width:386px">Our certifications reflect Kestrada's commitment to the highest standards of quality, safety, and compliance. As a Service-Disabled Veteran-Owned Small Business (SDVOSB), we meet strict federal requirements and bring veteran values of discipline and integrity to every project. Being fully licensed, insured, OSHA compliant, and federally/state certified ensures that our clients can trust us to deliver construction solutions that are reliable, safe, and procurement-ready.</p>
<ul class="checklist">
  <li><svg width="10" height="10" viewBox="0 0 10 10"><circle cx="5" cy="5" r="5" fill="#d1ad45"/><path d="M2.8 5.2l1.5 1.5 3-3" stroke="#fff" stroke-width="1.2" fill="none"/></svg>SDVOSB (Service-Disabled Veteran-Owned Small Business)</li>
  <li><svg width="10" height="10" viewBox="0 0 10 10"><circle cx="5" cy="5" r="5" fill="#d1ad45"/><path d="M2.8 5.2l1.5 1.5 3-3" stroke="#fff" stroke-width="1.2" fill="none"/></svg>Licensed &amp; Insured Contractor</li>
  <li><svg width="10" height="10" viewBox="0 0 10 10"><circle cx="5" cy="5" r="5" fill="#d1ad45"/><path d="M2.8 5.2l1.5 1.5 3-3" stroke="#fff" stroke-width="1.2" fill="none"/></svg>OSHA &amp; Safety Compliant</li>
  <li><svg width="10" height="10" viewBox="0 0 10 10"><circle cx="5" cy="5" r="5" fill="#d1ad45"/><path d="M2.8 5.2l1.5 1.5 3-3" stroke="#fff" stroke-width="1.2" fill="none"/></svg>Federal &amp; State Procurement Certified</li>
</ul>
<div class="abs" style="left:796px;top:2610px;width:228px;height:215px;background:var(--gold-light)"></div>
<div class="photo" role="img" aria-label="Smiling builder in a hard hat and orange vest holding a contract clipboard" style="left:641px;top:2631px;width:358px;height:444px;background:linear-gradient(170deg,#6f8db5,#a57a5a 45%,#e56f2c 75%,#c25a22)"></div>

<!-- contact -->
<svg class="abs" style="left:175px;top:3160px" width="430" height="430" viewBox="0 0 430 430"><path d="M30 280 A200 200 0 0 1 300 25" fill="none" stroke="#d1ad45" stroke-width="6"/></svg>
<div class="photo" role="img" aria-label="Site foreman on the phone pointing ahead while holding a clipboard" style="left:200px;top:3184px;width:390px;height:390px;border-radius:50%;background:radial-gradient(circle at 45% 40%,#d8dccd,#c9cf6a 60%,#8d9450)"></div>
<div class="abs" style="left:432px;top:3470px;width:112px;height:112px;border-radius:50%;background:#fff"></div>
<div class="brand" style="left:437px;top:3512px;font-size:15px;color:var(--gold)"><span class="dot" style="width:20px;height:20px"></span>Kestrada</div>

<h2 class="serif" style="left:668px;top:3190px">Get In Touch</h2>
<p class="body-text" style="left:668px;top:3248px;width:350px">Looking to partner with a reliable construction team for your next project? Contact Kestrada today.</p>
<div class="field" style="left:668px;top:3301px;width:166px">First Name*</div>
<div class="field" style="left:842px;top:3301px;width:165px">Last Name*</div>
<div class="field" style="left:668px;top:3347px;width:166px">Phone Number*</div>
<div class="field" style="left:842px;top:3347px;width:165px">Email Address*</div>
<div class="field" style="left:668px;top:3392px;width:339px;height:70px;border-radius:18px">Message*</div>
<div class="btn" style="left:668px;top:3493px;width:152px;height:37px">Submit Request</div>

<!-- footer -->
<svg class="abs" style="left:0;top:3578px" width="1200" height="160" viewBox="0 0 1200 160">
  <path d="M0 145 Q420 80 855 6 Q1040 80 1200 150 V160 H0Z" fill="#d1ad45"/>
  <path d="M0 154 Q420 92 855 14 Q1040 90 1200 160 Z" fill="#000"/>
</svg>
<footer class="abs" style="left:0;top:3736px;width:1200px;height:365px;background:#000">
  <div class="brand" style="left:204px;top:88px;font-size:22px;color:#fff"><span class="dot" style="width:34px;height:34px"></span>Kestrada</div>
  <div class="footer-col">
    <h5 style="left:454px;top:14px">Quick Links</h5>
    <a style="left:466px;top:44px">Home</a>
    <a style="left:466px;top:66px">About Us</a>
    <a style="left:466px;top:88px">Services</a>
    <a style="left:466px;top:110px">Clients</a>
    <a style="left:466px;top:132px">Certifications</a>
    <a style="left:466px;top:154px">Contact Us</a>
  </div>
  <div class="footer-col">
    <h5 style="left:635px;top:14px">Contact</h5>
    <svg class="abs" style="left:631px;top:46px" width="10" height="12" viewBox="0 0 10 12"><path d="M5 0a4 4 0 0 0-4 4c0 3 4 8 4 8s4-5 4-8a4 4 0 0 0-4-4z" fill="#d1ad45"/><circle cx="5" cy="4" r="1.4" fill="#000"/></svg>
    <span style="left:647px;top:44px">Lindenweg 18 10437 Berlin</span>
    <svg class="abs" style="left:630px;top:68px" width="11" height="11" viewBox="0 0 11 11"><path d="M2 0l2 3-1 1.5c.8 1.5 2 2.7 3.5 3.5L8 7l3 2-1 2C5 11 0 6 0 1z" fill="#d1ad45"/></svg>
    <span style="left:647px;top:66px">(+32)555-214</span>
    <svg class="abs" style="left:629px;top:90px" width="12" height="9" viewBox="0 0 12 9"><rect width="12" height="9" fill="#d1ad45"/><path d="M0 0l6 5 6-5" stroke="#000" fill="none"/></svg>
    <span style="left:647px;top:88px">info@kestrada-build.example</span>
  </div>
  <div class="footer-col">
    <h5 style="left:867px;top:14px">Services</h5>
    <a style="left:877px;top:44px">General Contracting</a>
    <a style="left:877px;top:66px">Design-Build Construction</a>
    <a style="left:877px;top:88px">Environmental Remediation</a>
    <a style="left:877px;top:110px">Disaster Recovery</a>
  </div>
  <div class="abs" style="left:156px;top:302px;width:888px;height:1px;background:#333"></div>
  <span class="abs" style="left:196px;top:328px;font-size:9px;color:#fff">copyright © 2025 Kestrada.</span>
  <span class="abs" style="left:829px;top:328px;font-size:9px;color:#fff">Privacy Policy | Terms &amp; Conditions</span>
</footer>
<span class="social" style="left:206px;background:var(--gold)"></span>
<span class="social" style="left:236px"></span>
<span class="social" style="left:268px"></span>
<span class="social" style="left:298px"></span>

</body>
</html>
```